Form Sculptors Business Card

Professional cosmetic surgery company, based in very exclusive area in London. High profiled clientele. Brand is very artistic, modern, state-of-the-art, safe. The best in the business. Celebrity clientele.

Form Sculptor’s of London is a brand serving a discriminating and exclusive clientele who value personal service that is both intimate and high end. Our clients choose Form Sculptors because of the relationships we share with all of our customers. The clients of Form Sculptors have an equal partnership between customers, and very experienced, highly qualified medical professionals. This together provides you with a professional service that keeps you looking good and feeling good. It is a relationship based on honesty, compassion, loyalty and respect.
Form Sculptor’s have provided services for internationally recognised celebrities, and other high profiled individuals.

The cards are used for networking at private, exclusive events with VIPs.

Target Market(s)

Professionals
Rich people

Industry/Entity Type

Professional Service

Contact Information for Business Card

Need double sided business card design for 4 people. Back of the business card needs to have contrast background to the front with butterfly watermark with services provided:
Hair Restoration surgery
Hair Loss treatments
Breast surgery
Rhinoplasty
Pulvix Liposuction
Fat Grafting
Lumaxin & Fillers

Front of the business card needs to be a nice satin black.
with following information:
Calvert Osterlund - name
Chief Executive - Job title

www.formsculptors-example.co.uk
calvert@formsculptors-example.co.uk
Phone: +44 (0)207 946 0321
Mobile: +44 (0)7700 900 147

The London Farrowmere Clinic
14 Farrowmere Lane | London | W1X 4QP
Off Quenby Street

All business cards have the same address, phone, website as Calvert's details.
Same details on the back of the business card as well.
The other cards have different name, job title, email, mobile number

Teodor Lunn - Name
Partner - Job Title
Former England International Cricketer - please include below job title

email: teodor@formsculptors-example.co.uk
mobile: +44(0)7700 900582

Dr Castello Vranesk - Name
Plastic Surgeon - Job Title
drvranesk@formsculptors-example.co.uk
No mobile number

Dr Ezra Tolquist FRCS (please put FRCS in small font) - Name
Hair Restoration Surgeon - Job Title
drtolquist@formsculptors-example.co.uk
No mobile number

Colors
cedeec
85abd2
0655a3

Requirements
Must have
• The logo needs to be in a metallic finish
• Text needs to be striking
• nice background
• butterfly watermark on the back

```html
<!DOCTYPE html>
<html lang="en">
<head>
<meta charset="utf-8">
<title>Form Sculptors Business Card</title>
<link rel="stylesheet" href="https://fonts.googleapis.com/css2?family=Tinos:wght@400;700&family=Arimo:wght@400&display=swap">
<style>
  :root {
    --backdrop: #5c3b27;
    --satin-black: #0b0b0b;
    --gold: #f4a623;
    --gold-deep: #e8961a;
    --white: #f4f4f4;
    --mark-grey: #4a4a4a;
    --ink: #111111;
  }
  html, body {
    margin: 0;
    padding: 0;
    width: 1200px;
    height: 914px;
    overflow: hidden;
    background: var(--backdrop);
  }
  .sheet {
    position: relative;
    width: 1200px;
    height: 914px;
  }
  .card {
    position: absolute;
    left: 230px;
    width: 740px;
    height: 410px;
    background: var(--satin-black);
    overflow: hidden;
    box-shadow: 0 8px 24px rgba(0,0,0,.45);
  }
  .card--back { top: 30px; }
  .card--front { top: 474px; }

  /* Back */
  .services-title {
    position: absolute;
    left: 44px;
    top: 30px;
    margin: 0;
    font: 700 28px "Tinos", serif;
    color: var(--gold);
  }
  .services-list {
    position: absolute;
    left: 60px;
    top: 88px;
    margin: 0;
    padding: 0;
    list-style: none;
    font: 400 21px "Arimo", sans-serif;
    color: var(--white);
    line-height: 32px;
  }
  .services-list li {
    position: relative;
    padding-left: 34px;
  }
  .services-list li::before {
    content: "";
    position: absolute;
    left: 4px;
    top: 11px;
    width: 10px;
    height: 10px;
    border-radius: 50%;
    background: var(--gold);
  }
  .watermark {
    position: absolute;
    right: 50px;
    top: 40px;
    width: 300px;
    height: 280px;
  }
  .back-band-line {
    position: absolute;
    left: 0; right: 0;
    bottom: 34px;
    height: 4px;
    background: var(--gold);
  }
  .back-band {
    position: absolute;
    left: 0; right: 0;
    bottom: 0;
    height: 26px;
    background: var(--gold);
  }

  /* Front */
  .brand {
    position: absolute;
    left: 150px;
    top: 30px;
    display: flex;
    align-items: center;
    gap: 12px;
    font: 700 38px "Tinos", serif;
    color: var(--gold);
    letter-spacing: 1px;
  }
  .brand-dot {
    width: 26px;
    height: 26px;
    border-radius: 50%;
    background: var(--gold);
  }
  .clinic {
    position: absolute;
    left: 40px;
    top: 108px;
    margin: 0;
    font: 700 27px "Tinos", serif;
    color: var(--gold);
  }
  .contacts {
    position: absolute;
    left: 40px;
    top: 160px;
    margin: 0;
    padding: 0;
    list-style: none;
    font: 400 19px "Arimo", sans-serif;
    color: var(--white);
  }
  .contacts li {
    display: flex;
    align-items: center;
    gap: 20px;
    height: 34px;
  }
  .contacts svg { width: 22px; height: 22px; flex: none; }
  .divider {
    position: absolute;
    left: 440px;
    top: 200px;
    width: 3px;
    height: 130px;
    background: var(--gold);
  }
  .person {
    position: absolute;
    left: 470px;
    top: 220px;
    width: 250px;
    text-align: center;
  }
  .person-name {
    margin: 0;
    font: 700 28px "Tinos", serif;
    color: var(--gold);
  }
  .person-title {
    margin: 4px 0 6px;
    font: 700 17px "Tinos", serif;
    color: var(--white);
  }
  .person-mobile {
    margin: 0;
    font: 400 19px "Arimo", sans-serif;
    color: var(--white);
  }
  .front-band-line {
    position: absolute;
    left: 0; right: 0;
    bottom: 62px;
    height: 4px;
    background: var(--gold);
  }
  .front-band {
    position: absolute;
    left: 0; right: 0;
    bottom: 0;
    height: 54px;
    background: var(--gold);
    border-bottom: 3px solid var(--ink);
    box-sizing: border-box;
    display: flex;
    align-items: center;
    padding-left: 40px;
    font: 400 21px "Arimo", sans-serif;
    color: var(--ink);
  }
</style>
</head>
<body>
<main class="sheet">

  <section class="card card--back" aria-label="Card back">
    <h2 class="services-title">services :-</h2>
    <ul class="services-list">
      <li>Hair Restoration surgery</li>
      <li>Hair Loss treatments</li>
      <li>Breast surgery</li>
      <li>Rhinoplasty</li>
      <li>Pulvix Liposuction</li>
      <li>Fat Grafting</li>
      <li>Lumaxin &amp; Fillers</li>
    </ul>
    <svg class="watermark" role="img" aria-label="Large faint butterfly watermark" viewBox="0 0 300 280">
      <defs>
        <radialGradient id="markFade" cx="50%" cy="45%" r="60%">
          <stop offset="0%" stop-color="#4a4a4a" stop-opacity=".75"/>
          <stop offset="100%" stop-color="#4a4a4a" stop-opacity="0"/>
        </radialGradient>
      </defs>
      <rect x="0" y="0" width="300" height="280" rx="40" fill="url(#markFade)"/>
    </svg>
    <div class="back-band-line"></div>
    <div class="back-band"></div>
  </section>

  <section class="card card--front" aria-label="Card front">
    <div class="brand"><span class="brand-dot"></span>Form Sculptors</div>
    <h1 class="clinic">The London Farrowmere Clinic</h1>
    <ul class="contacts">
      <li>
        <svg viewBox="0 0 24 24" aria-hidden="true"><path fill="#f4a623" d="M3 9c0-3 4-5 9-5s9 2 9 5l-4 1-1-3H8L7 10zM6 11h12l2 9H4z"/><circle cx="12" cy="15" r="2.5" fill="#0b0b0b"/></svg>
        +44 (0)207 946 0321
      </li>
      <li>
        <svg viewBox="0 0 24 24" aria-hidden="true"><circle cx="12" cy="12" r="9" fill="none" stroke="#f4a623" stroke-width="2"/><path d="M3 12h18M12 3c-4 4-4 14 0 18M12 3c4 4 4 14 0 18" fill="none" stroke="#f4a623" stroke-width="1.6"/></svg>
        www.formsculptors-example.co.uk
      </li>
      <li>
        <svg viewBox="0 0 24 24" aria-hidden="true"><rect x="2" y="6" width="20" height="13" fill="#f4a623"/><path d="M2 6l10 7 10-7" fill="none" stroke="#0b0b0b" stroke-width="1.5"/></svg>
        calvert@formsculptors-example.co.uk
      </li>
    </ul>
    <div class="divider"></div>
    <div class="person">
      <p class="person-name">Calvert Osterlund</p>
      <p class="person-title">Chief Executive</p>
      <p class="person-mobile">+44 (0)7700 900 147</p>
    </div>
    <div class="front-band-line"></div>
    <div class="front-band">14 Farrowmere Lane | London | W1X 4QP Off Quenby Street</div>
  </section>

</main>
</body>
</html>
```